Business Card Design

WE are looking for a premium quality Business Cards for a Law Firm . Copies of our current business card is attached.

Contact Information for Business Card

xyz

```html
<!DOCTYPE html>
<html lang="en">
<head>
<meta charset="utf-8">
<title>Hartwell Lawyers – Business Card</title>
<link rel="stylesheet" href="https://fonts.googleapis.com/css2?family=Tinos:wght@400;700&display=swap">
<style>
  :root {
    --backdrop: #333333;
    --card: #ffffff;
    --forest: #0f2a1f;
    --gold: #c9a862;
    --ink: #111111;
  }
  * { margin: 0; padding: 0; box-sizing: border-box; }
  html, body {
    width: 1200px; height: 780px; overflow: hidden;
    background: var(--backdrop);
    font-family: "Tinos", "Times New Roman", serif;
  }
  .stage {
    position: relative; width: 1200px; height: 780px;
    display: flex; align-items: center; justify-content: center; gap: 40px;
  }
  .card {
    position: relative; width: 540px; height: 309px;
    background: var(--card);
    box-shadow: 0 10px 24px rgba(0,0,0,0.35);
    overflow: hidden;
  }

  /* brand mark */
  .brand { position: absolute; display: flex; flex-direction: column; align-items: center; }
  .brand-ring { border: 4px solid var(--gold); border-radius: 50%; }
  .brand-name {
    color: var(--forest); font-weight: 700; letter-spacing: 1px;
    white-space: nowrap; line-height: 1;
  }

  .card-back .brand { left: 0; right: 0; top: 70px; }
  .card-back .brand-ring { width: 90px; height: 90px; }
  .card-back .brand-name { font-size: 34px; margin-top: 22px; }

  .card-front .brand { left: 200px; width: 260px; top: 26px; }
  .card-front .brand-ring { width: 62px; height: 62px; }
  .card-front .brand-name { font-size: 23px; margin-top: 14px; }

  /* person */
  .person {
    position: absolute; right: 255px; top: 160px; text-align: right; white-space: nowrap;
  }
  .person-name { color: var(--gold); font-size: 30px; font-weight: 700; line-height: 1; letter-spacing: 0.5px; }
  .person-role { color: var(--ink); font-size: 12.5px; font-weight: 700; margin-top: 6px; }
  .person-credentials { color: var(--ink); font-size: 12.5px; font-weight: 700; margin-top: 2px; }

  .divider {
    position: absolute; left: 300px; top: 150px; width: 1.5px; height: 88px; background: #555;
  }

  /* contact list */
  .contacts { position: absolute; left: 315px; top: 150px; list-style: none; }
  .contacts li {
    display: flex; align-items: center; gap: 8px;
    font-size: 12px; font-weight: 700; color: var(--ink);
    height: 21px; white-space: nowrap;
  }
  .contacts svg { width: 12px; height: 12px; flex: none; }

  /* address band */
  .address-band {
    position: absolute; left: 0; right: 0; top: 252px; height: 32px;
    background: var(--gold); color: #ffffff;
    font-size: 13.5px; font-weight: 700;
    display: flex; align-items: center; padding-left: 28px; white-space: nowrap;
  }
</style>
</head>
<body>
<main class="stage">

  <section class="card card-back" aria-label="Card back">
    <div class="brand">
      <div class="brand-ring"></div>
      <div class="brand-name">HARTWELL LAWYERS</div>
    </div>
  </section>

  <section class="card card-front" aria-label="Card front">
    <div class="brand">
      <div class="brand-ring"></div>
      <div class="brand-name">HARTWELL LAWYERS</div>
    </div>

    <div class="person">
      <div class="person-name">DANIEL MERCER</div>
      <div class="person-role">Director and Principal Solicitor</div>
      <div class="person-credentials">MBA, Juris Doctor</div>
    </div>

    <div class="divider"></div>

    <ul class="contacts">
      <li>
        <svg viewBox="0 0 24 24" aria-hidden="true"><path fill="#c9a862" d="M6.6 10.8a15.1 15.1 0 0 0 6.6 6.6l2.2-2.2a1 1 0 0 1 1-.25 11.4 11.4 0 0 0 3.6.57 1 1 0 0 1 1 1V20a1 1 0 0 1-1 1A17 17 0 0 1 3 4a1 1 0 0 1 1-1h3.5a1 1 0 0 1 1 1c0 1.25.2 2.45.57 3.6a1 1 0 0 1-.25 1z"/></svg>
        +61 7 3000 4172
      </li>
      <li>
        <svg viewBox="0 0 24 24" aria-hidden="true"><rect x="6" y="2" width="12" height="20" rx="2" fill="none" stroke="#c9a862" stroke-width="2"/><circle cx="12" cy="18" r="1.2" fill="#c9a862"/></svg>
        +61 0400 318 627
      </li>
      <li>
        <svg viewBox="0 0 24 24" aria-hidden="true"><circle cx="12" cy="12" r="9" fill="none" stroke="#c9a862" stroke-width="2"/><path d="M3 12h18M12 3c3 3 3 15 0 18M12 3c-3 3-3 15 0 18" fill="none" stroke="#c9a862" stroke-width="1.6"/></svg>
        www.hartwelllawyers.com.au
      </li>
      <li>
        <svg viewBox="0 0 24 24" aria-hidden="true"><rect x="2" y="5" width="20" height="14" rx="1.5" fill="none" stroke="#c9a862" stroke-width="2"/><path d="M2.5 6l9.5 7 9.5-7" fill="none" stroke="#c9a862" stroke-width="2"/></svg>
        daniel@hartwelllawyers.com.au
      </li>
    </ul>

    <div class="address-band">Level 3, Hartwell House, 88 Ridge Terrace, Fernvale Hill, QLD 4000</div>
  </section>

</main>
</body>
</html>
```